Tandem Hearth Works Pty Ltd

We need business cards for a company based in Perth, we install, service and maintain fire equipment.
On the front we want a great design with our logo and a small spot for our full company name, general company email address and office number. On the back we need space for our name, title, mobile number and email address on the back.

Target Market(s)

Facility managers and commercial/industrial building owners/occupiers.

Contact Information for Business Card

Font styles to use
Sans Serif

Requirements
Must have
• Please only submit 5 of your best samples.
Darker tones are preferred.
Nice to have
• We want to use, black, red and grey. Keep it modern and clean.
I've attached the company logo and a sample of a boarder we use on our emergency plans.
Should not have
• No preference. Let the designer choose.

```html
<!DOCTYPE html>
<html lang="en">
<head>
<meta charset="utf-8">
<title>Tandem Hearth Works – Business Cards</title>
<link rel="stylesheet" href="https://fonts.googleapis.com/css2?family=Roboto:wght@400;700;900&display=swap">
<style>
  :root {
    --fire-red: #ec1c24;
    --paper: #ffffff;
    --ink: #2b2b2b;
    --backdrop: #dcdcdc;
    --shadow: rgba(0, 0, 0, 0.28);
  }
  * { margin: 0; padding: 0; box-sizing: border-box; }
  html, body {
    width: 1200px; height: 900px; overflow: hidden;
    background: var(--backdrop);
    font-family: "Roboto", Arial, sans-serif;
  }
  .canvas { position: relative; width: 1200px; height: 900px; }

  .card {
    position: absolute; top: 216px;
    width: 309px; height: 501px;
    overflow: hidden;
    box-shadow: 2px 3px 4px var(--shadow);
  }
  .card--front {
    left: 279px;
    background: var(--fire-red);
    color: var(--paper);
    border-radius: 0 62px 0 62px;
  }
  .card--back {
    left: 617px;
    background: var(--paper);
    color: var(--ink);
    border-radius: 62px 0 62px 0;
  }

  .wordmark {
    position: absolute; left: 0; right: 0; top: 114px;
    text-align: center;
    font-weight: 900; font-size: 40px; line-height: 1.05;
    letter-spacing: 1px; text-transform: uppercase;
  }
  .card--front .wordmark { color: var(--paper); }
  .card--back .wordmark { color: var(--fire-red); }

  .company-name {
    position: absolute; left: 33px; top: 302px;
    font-weight: 700; font-size: 20px; line-height: 24px;
    text-transform: uppercase;
  }
  .office-phone {
    position: absolute; left: 33px; top: 367px;
    font-weight: 700; font-size: 23px;
  }
  .front-links {
    position: absolute; left: 35px; top: 421px;
    list-style: none; font-size: 16px; line-height: 20px;
  }
  .front-links li { display: flex; align-items: center; gap: 8px; white-space: nowrap; }
  .front-links svg { width: 16px; height: 14px; flex: none; }

  .person-name {
    position: absolute; left: 35px; top: 332px;
    font-weight: 700; font-size: 25px; color: var(--fire-red);
    text-transform: uppercase;
  }
  .person-title {
    position: absolute; left: 35px; top: 361px;
    font-size: 20px; color: var(--ink);
  }
  .back-links {
    position: absolute; left: 34px; top: 407px;
    list-style: none; font-size: 20px; line-height: 25px; color: var(--ink);
  }
  .back-links li { display: flex; align-items: center; gap: 8px; white-space: nowrap; }
  .back-links svg { width: 19px; height: 19px; flex: none; }
</style>
</head>
<body>
<main class="canvas">

  <section class="card card--front" aria-label="Business card front">
    <div class="wordmark">Tandem<br>Hearth</div>
    <h1 class="company-name">Tandem Hearth<br>Works Pty Ltd</h1>
    <p class="office-phone">789.555.0142</p>
    <ul class="front-links">
      <li>
        <svg viewBox="0 0 16 12" aria-hidden="true"><rect x="0.5" y="0.5" width="15" height="11" fill="var(--paper)"/><path d="M0.5 0.5 L8 7 L15.5 0.5 M0.5 11.5 L6 6 M15.5 11.5 L10 6" stroke="var(--fire-red)" stroke-width="1.2" fill="none"/></svg>
        info@thworks.com
      </li>
      <li>
        <svg viewBox="0 0 16 16" aria-hidden="true"><g fill="none" stroke="var(--paper)" stroke-width="1.4"><circle cx="8" cy="8" r="7"/><ellipse cx="8" cy="8" rx="3" ry="7"/><path d="M1 8 H15 M2.5 4.5 H13.5 M2.5 11.5 H13.5"/></g></svg>
        www.thworks.com
      </li>
    </ul>
  </section>

  <section class="card card--back" aria-label="Business card back">
    <div class="wordmark">Tandem<br>Hearth</div>
    <h2 class="person-name">Marcus Hale</h2>
    <p class="person-title">Managing Director</p>
    <ul class="back-links">
      <li>
        <svg viewBox="0 0 19 19" aria-hidden="true"><rect x="4.5" y="1" width="10" height="17" rx="1.8" fill="none" stroke="var(--fire-red)" stroke-width="1.8"/><circle cx="9.5" cy="15" r="1" fill="var(--fire-red)"/></svg>
        789.555.0187
      </li>
      <li>
        <svg viewBox="0 0 19 19" aria-hidden="true"><rect x="1" y="4" width="17" height="12" fill="var(--fire-red)"/><path d="M1 4 L9.5 11 L18 4 M1 16 L7 10 M18 16 L12 10" stroke="var(--paper)" stroke-width="1.2" fill="none"/></svg>
        marcus@thworks.com
      </li>
    </ul>
  </section>

</main>
</body>
</html>
```